IT Company needs Website for new Web and Mobile products for Sports and Fitness

Background:

We developed web based white label frontend web solution, backend services and white label mobile apps for to log, analyze, share and control sport and fitness activities. The name of this product suite is "Trevantix" (http://trevantix-example.com)

This products will be used by customers that provide platforms and community systems for sport and fitness. One of the major USP's is, that our technology i open for nearly all common formats, devices and apps out in the market. This means, you can just upload your data directly from device, file or app - e.G. Kestrel, Bolvane, Ravelo, StrideVault, Pacelumo, Zembra and much others.

Two current concrete examples/References

(1) MyQuorel
It's an international platform from quorel for runners. It provides individual training lans and a training log. MyQuorel uses the Backend Product "Trevantix Hub" (see http://hub.trevantix-example.net for a landing page) to integrate device, file and app support. Before this, every user has to track his training with manual inputs

(2) Paceharbor and fen-zine
Both are German customers. Paceharor is focused on runners. fen-zine is focused on Triatheletes. Both use the Product "Trevantix Web". This is a complete web solution with web based frontend solutions for athletes and coaches.

What do we need?
We need website layout for B2B for our products. We don't need lot's of pages. We need the pretty and nice layout, so we can derive the pages we need.

IMPORTANT
We don't talk about the webpages for the product itself (this will be a different project in future). We talk about a website, explaining the products)
Updates

Hi all,

we just start reviewing the first designs, and try to give feedback as detailed as possible. We attached a PDF document, to describe the the products a little bit more detailed. 

As written in the description, in the end we have two different sections. One is the usual stuff like "start page", "about", "contact", "disclaimer", "pricing", "blah...." and one will be the Developer Section, the "Tec Section". This ist aimed to developers (of our customers) that will integrate our products in there existing system or which will integrate our services in there own software.  This "pages" are more like "documentation", so easy to read and cool to look at (cause developers likes it cool, but straight)

Dear all,

we just do the final review. Cause this week is with heavy load, it takes some time...

Cheers

Odell

Target Market(s)

* Platforms and Communities for sport, health and fitness
* Gyms

Industry/Entity Type

Concrete

Font styles to use
Sans Serif

Requirements
Must have
• * Templates shall base on bootstrap. If not, it shall be easily realized on our site with bootstrap or out of the box "full responsive"

* HTML5 / CSS3
Nice to have
• PAGES
- Start Page
- Generic Template (from which we can derive additional pages)
- Contact Page
- Disclaimer Page
- Blog/News Page
- "About us" Page (can be combined with disclaimer)
- One Example product page (in end we have 3 products), shall show (if you need product details, let me know)
- product and it's description
- pricing information
- Add-Ons for the product
- Developer Section Page (Start Point for developers, where the finde "basic technical concepts and developer API's
- Example Developer Page for technical concept
- Example Developer Page for API

LOGO ISSUE
You can use an align to the Logo attached OR provide a new logo. The given logo is a logo for our own B2C Website http://trevantix-example.net. It's not really necessary, that the logo or the color must be used for the product website. Maybe it will be better if it's a complete new one, to avoid irritation between Trevantix as a B2B product and trevantix-example.net as a B2C platform.
Should not have
• No Flash and other proprietary technologies

```html
<!DOCTYPE html>
<html lang="de">
<head>
<meta charset="utf-8">
<title>Trevantix – Digital Sport and Fitness Services</title>
<link href="https://fonts.googleapis.com/css2?family=PT+Sans:wght@400;700&family=PT+Sans+Narrow:wght@400;700&display=swap" rel="stylesheet">
<style>
:root{
  --orange:#e8841a;
  --orange-dark:#d26d0c;
  --link-red:#d2321e;
  --ink:#333;
  --ink-soft:#555;
  --line:#d9d9d9;
  --panel-bg:#fff;
  --tab-bg:#f1f1f3;
  --footer-bg:#252525;
  --footer-text:#cfcfcf;
}
*{margin:0;padding:0;box-sizing:border-box}
html,body{width:820px;height:1200px;overflow:hidden;background:#fff}
body{position:relative;font-family:"PT Sans",sans-serif;color:var(--ink)}
.abs{position:absolute}

/* header */
.site-header{position:absolute;left:0;top:0;width:820px;height:62px;background:#fff}
.brand{position:absolute;left:124px;top:10px}
.brand-name{font-size:20px;font-weight:700;color:var(--orange);line-height:1;display:flex;align-items:center;gap:5px}
.brand-name i{display:inline-block;width:12px;height:12px;border-radius:50%;background:var(--orange)}
.brand-tag{font-size:5px;font-weight:700;color:#222;margin-top:6px;letter-spacing:.1px;text-transform:uppercase}
.main-nav{position:absolute;left:280px;top:26px;display:flex}
.main-nav a{font-size:7px;color:#555;text-decoration:none;text-transform:uppercase;padding:0 18px;line-height:16px;border-left:1px solid #ddd}
.main-nav a:first-child{border-left:0}

/* hero */
.hero{position:absolute;left:0;top:62px;width:820px;height:290px;
  background:radial-gradient(ellipse at 18% 20%,#fff2c9 0%,#f6c26a 28%,#e08c3a 58%,#b5532a 100%)}
.hero-photo{position:absolute;right:80px;top:0;width:300px;height:290px;
  background:radial-gradient(ellipse at 55% 75%,rgba(220,40,40,.55),rgba(180,60,40,0) 60%)}
.hero-title{position:absolute;left:124px;top:81px;font-family:"PT Sans Narrow",sans-serif;font-size:22px;line-height:27px;text-transform:uppercase}
.hero-title .l1{color:var(--orange-dark)}
.hero-title .l2{color:#3a3a3a}
.signup{position:absolute;left:123px;top:147px;width:261px;height:27px;background:#fff;border:1px solid #cfcfcf;border-radius:2px}
.signup span{position:absolute;left:10px;top:9px;font-size:6.5px;color:#888}
.signup button{position:absolute;right:1px;top:1px;width:90px;height:23px;border:0;border-radius:2px;background:linear-gradient(#f3a825,#d97a0a);color:#fff;font-family:inherit;font-size:10px}
.hero-arrow{position:absolute;top:123px}
.hero-dot{position:absolute;left:668px;top:275px;width:7px;height:7px;border-radius:50%;background:#e6e6e6}

/* products */
.section-title{position:absolute;left:145px;top:371px;font-family:"PT Sans Narrow",sans-serif;font-weight:700;font-size:15px;color:#222}
.section-title em{font-style:normal;color:var(--orange)}
.section-rule{position:absolute;left:140px;top:402px;width:300px;height:4px;background:radial-gradient(ellipse at center,rgba(0,0,0,.07),transparent 70%)}
.panel{position:absolute;left:140px;top:427px;width:553px;height:697px;background:var(--panel-bg);border:1px solid var(--line);border-radius:3px;box-shadow:0 0 6px rgba(0,0,0,.06)}
.tab{position:absolute;left:23px;width:166px;height:38px;background:linear-gradient(#fafafb,var(--tab-bg));border:1px solid #dcdcdc;border-radius:2px;font-size:11.5px;color:#222;padding-left:12px;line-height:37px}
.tab.active{color:var(--orange)}
.topic{position:absolute;left:218px;font-size:13px;color:#333;display:flex;align-items:center}
.topic::before{content:"";width:7px;height:7px;border-radius:50%;background:var(--orange);margin-right:6px;box-shadow:0 0 0 1px #fbd4a8}
.sub{position:absolute;left:238px;font-size:11px;color:#222}
.thumb{position:absolute;border:2px solid #d4d4d4;border-radius:3px}
.copy{position:absolute;font-size:7px;line-height:10.4px;color:#444}
.more{display:block;color:var(--link-red);margin-top:5px;margin-left:3px}
.copy.wide .more{margin-left:0;margin-top:2px}

/* footer */
.site-footer{position:absolute;left:0;top:1144px;width:820px;height:56px;background:var(--footer-bg)}
.social{position:absolute;left:143px;top:15px;display:flex;gap:7.6px}
.social span{width:15px;height:15px;border-radius:2px;display:block}
.copyright{position:absolute;right:156px;top:13px;font-size:7px;color:var(--footer-text)}
</style>
</head>
<body>

<header class="site-header">
  <div class="brand">
    <div class="brand-name"><i></i>Trevantix</div>
    <div class="brand-tag">Digital sport and fitness services</div>
  </div>
  <nav class="main-nav">
    <a href="#">Home</a><a href="#">Trevantix</a><a href="#">Fitness Cloud</a><a href="#">References</a><a href="#">Products</a><a href="#">Services</a>
  </nav>
</header>

<section class="hero">
  <div class="hero-photo" role="img" aria-label="Runner's legs in red running shoes on a sunlit track"></div>
  <h1 class="hero-title"><span class="l1">Die offene Sport- und</span><br><span class="l2">Fitnessplatform fur jeden Sport</span></h1>
  <div class="signup"><span>WHAT'S YOUR EMAIL ADDRESS :</span><button>JOIN FOR FREE</button></div>
  <svg class="hero-arrow" style="left:59px" width="30" height="30" viewBox="0 0 30 30"><circle cx="15" cy="15" r="13.5" fill="rgba(255,255,255,.15)" stroke="rgba(255,255,255,.75)" stroke-width="1.5"/><path d="M17 9 L11 15 L17 21" fill="none" stroke="rgba(255,255,255,.85)" stroke-width="2"/></svg>
  <svg class="hero-arrow" style="left:738px" width="30" height="30" viewBox="0 0 30 30"><circle cx="15" cy="15" r="13.5" fill="rgba(255,255,255,.15)" stroke="rgba(255,255,255,.75)" stroke-width="1.5"/><path d="M13 9 L19 15 L13 21" fill="none" stroke="rgba(255,255,255,.85)" stroke-width="2"/></svg>
  <div class="hero-dot"></div>
</section>

<h2 class="section-title">Our <em>Products</em></h2>
<div class="section-rule"></div>

<section class="panel">
  <div class="tab" style="top:21px">Trevantix Hub</div>
  <div class="tab" style="top:68px">Trevantix Web</div>
  <div class="tab active" style="top:116px">Device Communication Agent</div>
  <div class="tab" style="top:163px">Trevantix Mobile App</div>

  <div class="topic" style="top:20px">Retrieve Data From Devices</div>

  <div class="sub" style="top:45px">Sport Watches</div>
  <div class="thumb" style="left:238px;top:66px;width:133px;height:74px;background:linear-gradient(90deg,#5b5b5b,#2a2a2a 45%,#8a3b6a 75%,#c04a8a)" role="img" aria-label="Two GPS sport watches"></div>
  <p class="copy" style="left:382px;top:66px;width:158px">Sed ut perspiciatis unde omnis iste natus error sit voluptatem accusantium doloremque laudan-tium, totam rem aperiam, eaque ipsa quae ab illo inventore veritatis et quasi architecto beatae vitae dicta sunt explicabo.<a class="more">Know More&gt;&gt;</a></p>

  <div class="sub" style="top:157px">Cardio Devices</div>
  <div class="thumb" style="left:238px;top:178px;width:133px;height:74px;background:linear-gradient(90deg,#e9e9e9,#3a3a3a 20%,#eaeaea 45%,#2f2f2f 58%,#eaeaea 70%,#3a3a3a 90%,#e9e9e9)" role="img" aria-label="Heart rate monitor devices"></div>
  <p class="copy" style="left:382px;top:178px;width:158px">Sed ut perspiciatis unde omnis iste natus error sit voluptatem accusantium doloremque laudan-tium, totam rem aperiam, eaque ipsa quae ab illo inventore veritatis et quasi architecto beatae vitae dicta sunt explicabo.<a class="more">Know More&gt;&gt;</a></p>

  <div class="sub" style="top:269px">Sport- and Fitness Tracker</div>
  <div class="thumb" style="left:238px;top:290px;width:133px;height:74px;background:radial-gradient(ellipse at 40% 60%,#3a3a3a,#0f0f0f 70%)" role="img" aria-label="Black fitness tracker wristband"></div>
  <p class="copy" style="left:382px;top:290px;width:158px">Sed ut perspiciatis unde omnis iste natus error sit voluptatem accusantium doloremque laudan-tium, totam rem aperiam, eaque ipsa quae ab illo inventore veritatis et quasi architecto beatae vitae dicta sunt explicabo.<a class="more">Know More&gt;&gt;</a></p>

  <div class="topic" style="top:390px">Send Data (e.g. Plans) planned for 2014</div>
  <div class="thumb" style="left:240px;top:411px;width:95px;height:54px;background:linear-gradient(#8fa7a0,#6f7d55 55%,#5a5a5a)" role="img" aria-label="Woman running on a road"></div>
  <p class="copy wide" style="left:341px;top:413px;width:196px">Sed ut perspiciatis unde omnis iste natus error sit voluptatem accusantium doloremque laudantium, totam rem aperiam, eaque ipsa quae ab illo inventore veritatis et quasi architecto beatae vitae dicta sunt explicabo.<a class="more">Know More&gt;&gt;</a></p>

  <div class="topic" style="top:490px">Direct accessible via Webbrowser</div>
  <div class="thumb" style="left:240px;top:511px;width:95px;height:54px;background:linear-gradient(90deg,#6f8d5a,#c9c9c9 50%,#e8e8e8)" role="img" aria-label="Web application screens on devices"></div>
  <p class="copy wide" style="left:341px;top:513px;width:196px">Sed ut perspiciatis unde omnis iste natus error sit voluptatem accusantium doloremque laudantium, totam rem aperiam, eaque ipsa quae ab illo inventore veritatis et quasi architecto beatae vitae dicta sunt explicabo.<a class="more">Know More&gt;&gt;</a></p>

  <div class="topic" style="top:584px">Mobile Agent planned for 2014</div>
  <div class="thumb" style="left:240px;top:605px;width:95px;height:54px;background:linear-gradient(90deg,#0f0f14,#1d2a3a 55%,#5b8bb0)" role="img" aria-label="Smartphone showing a fitness app next to a tracker"></div>
  <p class="copy wide" style="left:341px;top:607px;width:196px">Sed ut perspiciatis unde omnis iste natus error sit voluptatem accusantium doloremque laudantium, totam rem aperiam, eaque ipsa quae ab illo inventore veritatis et quasi architecto beatae vitae dicta sunt explicabo.<a class="more">Know More&gt;&gt;</a></p>
</section>

<footer class="site-footer">
  <div class="social">
    <span style="background:#3b5998"></span>
    <span style="background:#2fa9e0"></span>
    <span style="background:#555"></span>
    <span style="background:#f39a1e"></span>
    <span style="background:#c4302b"></span>
    <span style="background:#7a8fa6"></span>
  </div>
  <p class="copyright">© 2013 trevantix-example.com, All rights reserved</p>
</footer>

</body>
</html>
```